Webdesign für Heilpraktiker
Zielgruppe
Ich bin Heilpraktiker und betreibe eine Naturheilpraxis mit den Schwerpunkten der traditionellen chinesischen Medizin (TCM). Da ganz besonders in der Philosophie (sogenannte 'Schule' des Wo Shen). Aber auch in der traditionellen Heilweise der TCM, wie Akupunktur, Heilkräutermedizin und weiteres.
Die Zielgruppe sind Menschen, die medizinische Hilfe benötigen. (Vom Kind bis zum älteren Menschen).
Aufgabenstellung
Es gibt ein Praxislogo, ein Foto von mir und ggf. ein Landschaftsbild. Ich dachte an fünf Hauptseiten mit Untergruppen. Am Ende sollte alles in Wordpress formatiert werden können, um es zu veröffentlichen.
Weitere Fotos zur Unterstützung der Themen kann ich natürlich gerne liefern.
Die Gestaltung ist nicht festgesetzt. Sollte aber seriös rüber kommen.

```html
<!DOCTYPE html>
<html lang="de">
<head>
<meta charset="utf-8">
<title>Naturheilpraxis Fellnroth</title>
<link href="https://fonts.googleapis.com/css2?family=Cormorant+Garamond:wght@400;500&family=Open+Sans:ital,wght@0,300;0,400;1,300&family=Cabin:wght@400;600&display=swap" rel="stylesheet">
<style>
  :root{
    --paper:#f1efeb;
    --paper-dark:#e9e5df;
    --gold:#c9a95a;
    --gold-text:#f6eedb;
    --ink:#2a2a2a;
    --heading:#5a5550;
    --body:#4d4a46;
    --footer:#2b2725;
    --white:#ffffff;
  }
  *{margin:0;padding:0;box-sizing:border-box}
  html,body{width:1200px;height:3358px;overflow:hidden;background:var(--paper)}
  body{position:relative;font-family:"Cabin",sans-serif;color:var(--body)}
  .abs{position:absolute}
  .brand{left:500px;top:28px;width:200px;height:110px;display:flex;flex-direction:column;align-items:center;justify-content:center;gap:8px}
  .brand-dot{width:46px;height:46px;border:2px solid var(--ink);border-radius:50%}
  .brand-name{font-family:"Cabin",sans-serif;font-size:17px;color:var(--ink);letter-spacing:1px}
  .nav{top:166px;left:0;width:1200px;display:flex;justify-content:center;gap:24px;font-family:"Open Sans",sans-serif;font-size:19px;color:var(--ink)}
  .nav span{white-space:nowrap}
  .hero-photo{left:0;top:220px;width:592px;height:403px;background:linear-gradient(160deg,#5d6b2e 0%,#8a6a35 45%,#7a3f22 80%,#4d3a1c 100%)}
  .hero-quote{left:592px;top:271px;width:608px;height:352px;background:linear-gradient(135deg,#cdae61,#c3a252 60%,#cbac5f)}
  .quote{left:0;top:100px;width:608px;text-align:center;font-family:"Open Sans",sans-serif;font-weight:300;font-size:22px;line-height:38px;color:var(--gold-text)}
  .quote-src{left:250px;top:198px;font-family:"Open Sans",sans-serif;font-style:italic;font-weight:300;font-size:20px;color:var(--gold-text)}
  .person{left:0;top:623px;width:1200px;height:504px;background:var(--paper)}
  h2{font-family:"Cormorant Garamond",serif;font-weight:400;color:var(--heading);font-size:35px;letter-spacing:.5px;text-align:center;white-space:nowrap}
  .text{font-size:16.5px;line-height:31px;text-align:center;color:var(--body)}
  .signature{left:262px;top:296px;width:260px;height:72px;background:linear-gradient(90deg,rgba(60,55,50,.08),rgba(60,55,50,.16),rgba(60,55,50,.08));border-radius:36px}
  .portrait{left:825px;top:22px;width:302px;height:453px;background:linear-gradient(160deg,#6f6f72,#3f4044 55%,#25272d)}
  .content{left:0;top:1127px;width:1200px;height:1281px;background:linear-gradient(180deg,#ebe8e2 0%,#efece7 40%,#e8e4dd 70%,#edeae5 100%)}
  .circle{border-radius:50%;box-shadow:0 3px 8px rgba(0,0,0,.25)}
  .membership{left:0;top:2408px;width:1200px;height:360px;background:var(--paper)}
  .badge{left:547px;top:126px;width:125px;height:118px;background:#e4e8ef;border-radius:4px}
  .landscape{left:0;top:2768px;width:1200px;height:251px;background:linear-gradient(180deg,#b9c9d6 0%,#8fa474 35%,#7f9a3a 65%,#5f7a2c 100%)}
  .footer{left:0;top:3019px;width:1200px;height:339px;background:var(--footer)}
  .footer-mark{left:544px;top:32px;width:174px;height:174px;border-radius:50%;background:var(--white);display:flex;align-items:center;justify-content:center}
  .footer-mark span{font-size:17px;color:var(--ink);letter-spacing:1px}
  .footer-links{top:278px;left:0;width:1200px;text-align:center;font-family:"Open Sans",sans-serif;font-size:20px;color:var(--white);word-spacing:14px}
</style>
</head>
<body>
  <header>
    <div class="abs brand"><div class="brand-dot"></div><div class="brand-name">Praxis Fellnroth</div></div>
    <nav class="abs nav">
      <span>STARTSEITE</span>
      <span>ZU MEINER PERSON</span>
      <span>WOBEI KANN ICH HELFEN</span>
      <span>WAS IST DAS WO SHEN</span>
      <span>KONTAKT</span>
    </nav>
  </header>

  <section>
    <div class="abs hero-photo" role="img" aria-label="Fotografie eines alten, knorrigen Baumes im Wald"></div>
    <div class="abs hero-quote">
      <p class="abs quote">“Die Zweige geben Kunde<br>von der Wurzel.”</p>
      <p class="abs quote-src">Volksweisheit / Volksgut</p>
    </div>
  </section>

  <section class="abs person">
    <h2 class="abs" style="left:183px;top:82px;width:400px">ZU MEINER PERSON</h2>
    <p class="abs text" style="left:183px;top:212px;width:400px;line-height:30px">Heilpraktiker und zertifizierter<br>Therapeut der tradionellen chinesischen Medizin</p>
    <div class="abs signature" role="img" aria-label="Handschriftliche Unterschrift Kai Fellnroth"></div>
    <div class="abs portrait" role="img" aria-label="Porträtfoto des Heilpraktikers"></div>
  </section>

  <section class="abs content">
    <div class="abs circle" style="left:159px;top:105px;width:216px;height:216px;background:radial-gradient(circle at 45% 50%,#8fb05a,#4e7a30 60%,#3a4a28)" role="img" aria-label="Foto einer jungen Pflanze, die gegossen wird"></div>
    <h2 class="abs" style="left:584px;top:80px;width:400px">VITA</h2>
    <p class="abs text" style="left:484px;top:137px;width:600px;font-weight:600">Jahrgang 1967</p>
    <p class="abs text" style="left:434px;top:199px;width:700px">Seit 2015 zertifizierter TCM Therapeut (Berufsverband VNT e.V.)<br>Seit 2010 Gründer und Leiter des KFL Blutanalyselabors in Halvering<br>Seit 2006 Heilpraktiker in Halvering</p>
    <p class="abs text" style="left:434px;top:324px;width:700px;font-weight:600">Beschäftigung mit der Wo Shen Philosophie (Schule) seit 1988</p>

    <h2 class="abs" style="left:224px;top:493px;width:400px">WAS MACHE ICH</h2>
    <p class="abs text" style="left:131px;top:548px;width:600px">Seit vielen Jahrzehnten begeistere ich mich für die Themen der Medizin und die<br>Wiederherstellung der Gesundheit.<br>Ein grundlegendes Gesundheitssystem habe ich schon immer in der<br>traditionellen chinesischen Medizin gesehen.<br>Die traditionelle chinesische Medizin ist eine der ältesten Heilkunde- und<br>Therapieform der Welt. Unzählige Therapierichtungen, sogenannte „Schulen“,<br>sind im Laufe der vergangenen Jahrtausende entstanden.<br>Eine dieser Richtungen ist die Schule des „Wo Shen“. Diese besteht aus<br>philosophischen Betrachtungen, Erklärungsformen und konkreten<br>Therapieformen.</p>
    <div class="abs circle" style="left:854px;top:524px;width:212px;height:212px;background:radial-gradient(circle at 40% 45%,#e8e2d8,#a07a5c 60%,#6b4a35)" role="img" aria-label="Foto einer Akupunktur-Modellfigur"></div>

    <div class="abs circle" style="left:153px;top:974px;width:216px;height:216px;background:linear-gradient(135deg,#5f8fc4,#b9cde0 45%,#e7ebee)" role="img" aria-label="Foto der Fassade des Praxisgebäudes"></div>
    <h2 class="abs" style="left:625px;top:966px;width:400px">DIE PRAXIS</h2>
    <p class="abs text" style="left:511px;top:1033px;width:600px">Seit 2012 besteht die Praxis, in der sich auch das KFL Blutanalyselabor befindet,<br>im dritten Stock eines Wohn- und Geschäftshauses in der Halveringer<br>Innenstadt. Ein Aufzug ist vorhanden. Die Praxis ist gut mit öffentlichen<br>Verkehrsmitteln zu erreichen und hat in unmittelbarer Nähe auch ein Parkhaus.<br><em>(Tiefgarage und Haltstelle Lindenhof)</em></p>
  </section>

  <section class="abs membership">
    <h2 class="abs" style="left:403px;top:70px;width:400px;font-size:30px">MITGLIEDSCHAFT</h2>
    <div class="abs badge" role="img" aria-label="Mitgliedsabzeichen des Berufsverbands"></div>
  </section>

  <div class="abs landscape" role="img" aria-label="Panoramafoto einer grünen Hügellandschaft"></div>

  <footer class="abs footer">
    <div class="abs footer-mark"><span>Praxis Fellnroth</span></div>
    <p class="abs footer-links">IMPRESSUM DATENSCHUTZ</p>
  </footer>
</body>
</html>
```